Social Media Graphics - Oakline Push REVISED

Create 6-7 individual social media graphics (square size) to encourage folks to join our online course called:

The Harvest Ledger Circle
How to Launch a Multi-Million Business From Scratch
Sign Up Today!

IMPORTANT: Make the largest and most prominent text on the graphic be: How to Launch a Multi-Million Business From Scratch

For the color scheme of the graphics, let's try a blue color palette; make sure the graphics appeal to both men and women

Make sure each graphic contains 1 of the 3 pics attached (crop pic as needed); and make sure one of the graphics is all TEXT only.

Target Market(s)

men and women looking to start a business

Industry/Entity Type

Entrepreneurship

Colors
0054AA
0677BA
7BADD7
CADEEF
E8F1F8

Requirements
Must have
• All the text and use the 3 pics provided; one graphic can be all text; Simple, modern design that's easy to read

```html
<!DOCTYPE html>
<html lang="en">
<head>
<meta charset="utf-8">
<title>The Harvest Ledger Circle – Social Graphics</title>
<link rel="stylesheet" href="https://fonts.googleapis.com/css2?family=League+Gothic&display=swap">
<style>
  :root {
    --blue-deep: #0054aa;
    --blue-mid: #0677ba;
    --blue-soft: #7badd7;
    --blue-pale: #cadeef;
    --blue-mist: #e8f1f8;
    --badge-navy: #0b3f8f;
    --white: #ffffff;
    --photo-dark: #1d2a44;
    --photo-warm: #3b3a4c;
  }
  * { margin: 0; padding: 0; box-sizing: border-box; }
  html, body { width: 1200px; height: 902px; overflow: hidden; background: var(--white); }
  body { position: relative; font-family: "League Gothic", "Arial Narrow", sans-serif; }

  .tile { position: absolute; width: 312px; height: 312px; overflow: hidden; background: var(--blue-deep); color: var(--white); }
  .tile--one   { left: 119px; top: 143px; background: linear-gradient(120deg, var(--blue-deep) 10%, var(--blue-mid) 60%, var(--blue-deep)); }
  .tile--two   { left: 463px; top: 143px; background: linear-gradient(180deg, var(--blue-deep) 0%, var(--blue-deep) 55%, var(--blue-soft) 100%); }
  .tile--three { left: 807px; top: 143px; }
  .tile--four  { left: 119px; top: 485px; }
  .tile--five  { left: 463px; top: 485px; background: var(--blue-mid); }
  .tile--six   { left: 807px; top: 485px; }

  .course-label {
    position: absolute; display: flex; align-items: center; justify-content: center;
    color: var(--blue-deep); background: var(--white); white-space: nowrap; letter-spacing: 0.3px;
  }
  .course-label--pill { border-radius: 30px; }
  .course-label--outlined { border-radius: 30px; box-shadow: inset 0 0 0 3px var(--white), inset 0 0 0 5px var(--blue-deep); }
  .course-label--ghost { background: transparent; color: var(--white); border: 1.5px solid var(--white); border-radius: 20px; box-shadow: 0 3px 0 -1px var(--white); }
  .course-label--tab { border-left: 3px solid var(--white); border-right: 3px solid var(--white); box-shadow: inset 0 0 0 1.5px var(--blue-deep); }
  .course-label--boxed { background: var(--blue-deep); color: var(--white); border: 1.5px solid var(--white); border-radius: 3px; box-shadow: 3px 0 0 -1px var(--white); }

  .headline {
    position: absolute; left: 0; right: 0; text-align: center; font-weight: 400;
    text-transform: uppercase; letter-spacing: 0.2px;
  }
  .headline span { display: block; }

  .photo { position: absolute; }
  .photo--duo { background: linear-gradient(90deg, var(--photo-dark) 0%, var(--photo-warm) 45%, #2f4f8a 75%, var(--photo-dark) 100%); border-radius: 40px 40px 0 0; }
  .photo--duo-bright { background: linear-gradient(90deg, #1a1a1f 0%, #2a2a30 45%, #d9455f 55%, #e2536b 100%); border-radius: 40px 40px 0 0; }
  .photo--duo-bright-flip { background: linear-gradient(90deg, #e2536b 0%, #d9455f 45%, #26262c 55%, #1a1a1f 100%); border-radius: 40px 40px 0 0; }
  .photo--stage { background: linear-gradient(90deg, #223a73 0%, #2b4c8f 40%, #8a8680 60%, #6b6761 100%); border-radius: 30px 30px 0 0; }

  .signup-badge {
    position: absolute; border-radius: 50%; background: var(--badge-navy);
    box-shadow: 0 0 0 2px var(--white), 0 0 10px 3px rgba(255,255,255,0.55);
    display: flex; flex-direction: column; align-items: center; justify-content: center;
    text-align: center; color: var(--white); text-transform: uppercase;
    -webkit-text-stroke: 0.6px var(--badge-navy);
  }
  .signup-badge span { display: block; line-height: 0.88; }
</style>
</head>
<body>

  <section class="tile tile--one">
    <div class="course-label course-label--pill" style="left:26px; top:17px; width:259px; height:43px; font-size:25px;">THE HARVEST LEDGER CIRCLE</div>
    <h2 class="headline" style="top:68px; font-size:36px; line-height:37px;">
      <span>How to Launch a</span><span>Multi-Million Business</span><span>From Scratch</span>
    </h2>
    <div class="photo photo--duo" role="img" aria-label="Photo of the two course hosts standing side by side, arms crossed" style="left:146px; top:183px; width:155px; height:129px;"></div>
    <div class="signup-badge" style="left:26px; top:207px; width:76px; height:76px; font-size:30px;"><span>Sign Up</span><span>Today!</span></div>
  </section>

  <section class="tile tile--two">
    <div class="course-label" style="left:41px; top:20px; width:225px; height:36px; border-radius:3px; font-size:22px;">THE HARVEST LEDGER CIRCLE</div>
    <h2 class="headline" style="top:64px; font-size:38px; line-height:37px;">
      <span>How to Launch a</span><span>Multi-Million Business</span><span>From Scratch</span>
    </h2>
    <div class="photo photo--duo-bright" role="img" aria-label="Photo of the two course hosts smiling, arms crossed" style="left:41px; top:183px; width:131px; height:129px;"></div>
    <div class="signup-badge" style="left:202px; top:200px; width:76px; height:76px; font-size:30px;"><span>Sign Up</span><span>Today!</span></div>
  </section>

  <section class="tile tile--three">
    <div class="course-label course-label--tab" style="left:52px; top:0; width:207px; height:39px; font-size:21px;">THE HARVEST LEDGER CIRCLE</div>
    <h2 class="headline" style="top:54px; font-size:38px; line-height:40px;">
      <span>How to Launch a</span><span>Multi-Million Business</span><span>From Scratch</span>
    </h2>
    <div class="photo photo--duo" role="img" aria-label="Photo of the two course hosts standing together" style="left:142px; top:177px; width:153px; height:135px;"></div>
    <div class="signup-badge" style="left:56px; top:205px; width:60px; height:60px; font-size:24px;"><span>Sign Up</span><span>Today!</span></div>
  </section>

  <section class="tile tile--four">
    <div class="course-label course-label--outlined" style="left:39px; top:25px; width:230px; height:42px; font-size:23px;">THE HARVEST LEDGER CIRCLE</div>
    <h2 class="headline" style="top:79px; font-size:39px; line-height:40px;">
      <span>How to Launch a</span><span>Multi-Million Business</span><span>From Scratch</span>
    </h2>
    <div class="signup-badge" style="left:116px; top:213px; width:76px; height:76px; font-size:30px;"><span>Sign Up</span><span>Today!</span></div>
  </section>

  <section class="tile tile--five">
    <div class="course-label course-label--ghost" style="left:32px; top:14px; width:252px; height:34px; font-size:22px;">THE HARVEST LEDGER CIRCLE</div>
    <h2 class="headline" style="top:66px; font-size:38px; line-height:38px;">
      <span>How to Launch a</span><span>Multi-Million Business</span><span>From Scratch</span>
    </h2>
    <div class="photo photo--duo-bright-flip" role="img" aria-label="Photo of the two course hosts smiling together" style="left:69px; top:183px; width:142px; height:129px;"></div>
    <div class="signup-badge" style="left:234px; top:189px; width:58px; height:58px; font-size:23px;"><span>Sign Up</span><span>Today!</span></div>
  </section>

  <section class="tile tile--six">
    <div class="photo photo--stage" role="img" aria-label="Photo of the two course hosts speaking on stage" style="left:76px; top:8px; width:175px; height:80px;"></div>
    <div class="course-label course-label--boxed" style="left:52px; top:88px; width:209px; height:33px; font-size:21px;">THE HARVEST LEDGER CIRCLE</div>
    <h2 class="headline" style="top:134px; font-size:34px; line-height:35px;">
      <span>How to Launch a</span><span>Multi-Million Business</span><span>From Scratch</span>
    </h2>
    <div class="signup-badge" style="left:128px; top:244px; width:58px; height:58px; font-size:23px;"><span>Sign Up</span><span>Today!</span></div>
  </section>

</body>
</html>
```